Alaska Law Firm Needs a Sticker Design

We need a design for stickers to put on already-printed brochures. We mail the brochures to potential clients so they can learn more about accident-induced injuries, insurance claims, legal representation, and our own law firm.

One of our lawyers wrote a book that provides a helpful overview of personal injury claims. We are offering this book for free to anyone who calls and requests it. Therefore, the sticker design should include one of the following phrases, or something very similar:
a) "Still have questions? Call and request our book-- for free!"
b) "Still have questions about auto accident claims? Call and request our book today."
c) "Still have questions about filing a claim? Call and request a free copy of our book."
d) "Still have questions? Call us today to request a free copy of our book, Clear Lanes Ahead."
e) "To learn more about automobile accidents and insurance, call today and request a free copy of our book."

The sticker should be approximately 3"x3" and may be a circle, square, rectangle, or ellipsis. The sticker will be placed on the back of the folder, which is light blue. We would like the sticker to match the color scheme of our website and the folder.

I will upload an image of the book cover as soon as I obtain it.

Law Firm

Font styles to use
Serif
Sans Serif

Requirements
Should not have
• Bright colors that aren't already used in the folder design. e.g. no bright orange, pink, chartreuse, turquoise, yellow, red.

```html
<!DOCTYPE html>
<html lang="en">
<head>
<meta charset="utf-8">
<title>Still Have Questions Sticker</title>
<link rel="stylesheet" href="https://fonts.googleapis.com/css2?family=Exo+2:wght@600;700&family=Kurale&display=swap">
<style>
  :root {
    --navy: #1f2e86;
    --navy-deep: #172369;
    --ink: #232323;
    --paper: #ffffff;
    --mist: #e4e4e4;
    --bg-light: #f7f7f7;
    --bg-mid: #c9c9c9;
  }
  html, body {
    margin: 0;
    padding: 0;
    width: 1200px;
    height: 1200px;
    overflow: hidden;
  }
  body {
    background: linear-gradient(180deg, var(--bg-light) 0%, var(--bg-mid) 42%, var(--bg-light) 62%, var(--bg-light) 100%);
  }
  .sticker {
    display: block;
    width: 1200px;
    height: 1200px;
  }
  .sticker__rim { fill: var(--navy); }
  .sticker__face { fill: var(--paper); }
  .sticker__cap { stroke: var(--ink); stroke-width: 3; }
  .sticker__cap--top { fill: url(#capShine); }
  .sticker__cap--bottom { fill: var(--paper); }
  .sticker__band { fill: url(#bandShade); }
  .headline {
    font-family: "Exo 2", "Ubuntu", sans-serif;
    font-weight: 700;
    text-anchor: middle;
  }
  .headline__still { fill: var(--ink); }
  .headline__have { fill: var(--navy); }
  .headline--question {
    fill: var(--paper);
    font-size: 158px;
    filter: url(#textShadow);
  }
  .offer {
    font-family: "Kurale", "Gabriela", serif;
    text-anchor: middle;
  }
  .offer__line { fill: var(--ink); font-size: 60px; }
  .offer__free { fill: var(--navy); font-size: 104px; }
</style>
</head>
<body>
<svg class="sticker" viewBox="0 0 1300 1300" xmlns="http://www.w3.org/2000/svg" role="img" aria-label="Still have questions? Call and request our book for free!">
  <defs>
    <linearGradient id="capShine" x1="0" y1="0" x2="0" y2="1">
      <stop offset="0" stop-color="#d6d6d6"/>
      <stop offset="0.7" stop-color="#ececec"/>
      <stop offset="1" stop-color="#ffffff"/>
    </linearGradient>
    <linearGradient id="bandShade" x1="0" y1="0" x2="1" y2="0">
      <stop offset="0" stop-color="#1d2b7e"/>
      <stop offset="0.5" stop-color="#22338f"/>
      <stop offset="1" stop-color="#1a2670"/>
    </linearGradient>
    <clipPath id="faceClip">
      <circle cx="650" cy="650" r="497"/>
    </clipPath>
    <filter id="textShadow" x="-10%" y="-20%" width="120%" height="150%">
      <feDropShadow dx="0" dy="4" stdDeviation="4" flood-color="#000" flood-opacity="0.45"/>
    </filter>
  </defs>

  <circle class="sticker__rim" cx="650" cy="650" r="522"/>
  <circle class="sticker__face" cx="650" cy="650" r="497"/>

  <path class="sticker__cap sticker__cap--top" d="M182,553 A478 478 0 0 1 1118,553 Z"/>
  <rect class="sticker__band" x="100" y="572" width="1100" height="228" clip-path="url(#faceClip)"/>
  <path class="sticker__cap sticker__cap--bottom" d="M201,815 L1099,815 A478 478 0 0 1 201,815 Z"/>

  <text class="headline" x="645" y="475" font-size="150">
    <tspan class="headline__still">Still</tspan>
    <tspan class="headline__have">have</tspan>
  </text>
  <text class="headline headline--question" x="643" y="740">Questions?</text>

  <text class="offer offer__line" x="642" y="897">Call and request our book</text>
  <text class="offer offer__free" x="632" y="1012">for free!</text>
</svg>
</body>
</html>
```